MRT Property - Business Cards

Looking for a business card & general letterhead, signage etc design for our new logo.

Colours:
000a20
0056a2
00b5ef
0088ce
68cef2

Fonts:
Poppins
Karla

Please keep look and feel of new brand - example in the zip package I sent.

```html
<!DOCTYPE html>
<html lang="en">
<head>
<meta charset="UTF-8">
<title>MRT Property – Business Cards</title>
<link rel="stylesheet" href="https://fonts.googleapis.com/css2?family=Poppins:wght@400;600;800&display=swap">
<style>
  :root {
    --ink: #000a20;
    --brand-blue: #0056a2;
    --sky: #00b5ef;
    --mid-blue: #0088ce;
    --pale-blue: #68cef2;
    --white: #ffffff;
    --backdrop: #14161c;
  }
  * { margin: 0; padding: 0; box-sizing: border-box; }
  html, body { width: 1200px; height: 900px; overflow: hidden; }
  body {
    background: var(--backdrop);
    font-family: "Poppins", sans-serif;
    position: relative;
  }
  .card {
    position: absolute;
    left: 250px;
    width: 700px;
    height: 400px;
    border-radius: 30px;
    overflow: hidden;
    background: var(--brand-blue);
    box-shadow: 0 14px 30px rgba(0, 0, 0, 0.55);
  }
  .card--front { top: 35px; }
  .card--back { top: 465px; }

  .wordmark {
    position: absolute;
    color: var(--white);
    font-weight: 800;
    letter-spacing: 0.5px;
    line-height: 1;
  }
  .card--front .wordmark { left: 48px; top: 44px; font-size: 42px; }
  .card--back .wordmark { right: 48px; bottom: 48px; font-size: 38px; }

  .identity { position: absolute; left: 48px; top: 128px; }
  .identity__name {
    color: var(--sky);
    font-weight: 800;
    font-size: 30px;
    letter-spacing: 1px;
    text-transform: uppercase;
    line-height: 1.1;
  }
  .identity__role {
    color: var(--white);
    font-size: 16px;
    font-weight: 400;
    margin-top: 2px;
  }

  .contact { position: absolute; left: 48px; top: 218px; list-style: none; }
  .contact__item {
    display: flex;
    align-items: center;
    gap: 8px;
    color: var(--white);
    font-size: 15px;
    line-height: 26px;
  }
  .contact__icon { width: 14px; height: 14px; flex: none; }
  .contact__address {
    color: var(--white);
    font-size: 15px;
    line-height: 24px;
    margin-top: 8px;
    font-style: normal;
  }

  .swoosh-area {
    position: absolute;
    right: 0;
    bottom: 0;
    width: 370px;
    height: 290px;
    border-top-left-radius: 260px 290px;
    background: linear-gradient(135deg, var(--pale-blue) 0%, var(--mid-blue) 45%, var(--white) 78%);
  }

  .pattern-area {
    position: absolute;
    inset: 0;
    background: linear-gradient(135deg, #0a5fb8 0%, var(--brand-blue) 50%, #0b4f98 100%);
  }
</style>
</head>
<body>
  <section class="card card--front">
    <div class="wordmark">MRT Property</div>

    <div class="identity">
      <h1 class="identity__name">Dana Holt</h1>
      <p class="identity__role">Founder &amp; Principal</p>
    </div>

    <ul class="contact">
      <li class="contact__item">
        <svg class="contact__icon" viewBox="0 0 16 16" fill="none" stroke="#00b5ef" stroke-width="1.6"><path d="M4 1.5 6 5 4.5 6.5a9 9 0 0 0 5 5L11 10l3.5 2-1 2.5C7 14.5 1.5 9 1.5 2.5Z"/></svg>
        +1- 415-555-0134
      </li>
      <li class="contact__item">
        <svg class="contact__icon" viewBox="0 0 16 16" fill="none" stroke="#00b5ef" stroke-width="1.6"><rect x="1.5" y="3.5" width="13" height="9" rx="1"/><path d="m1.5 4 6.5 5 6.5-5"/></svg>
        info@mrtproperty.com
      </li>
      <li class="contact__item">
        <svg class="contact__icon" viewBox="0 0 16 16" fill="none" stroke="#00b5ef" stroke-width="1.4"><circle cx="8" cy="8" r="6.5"/><ellipse cx="8" cy="8" rx="2.8" ry="6.5"/><path d="M1.5 8h13"/></svg>
        www.mrtproperty.com
      </li>
      <li>
        <address class="contact__address">2140 Harbor Lane<br>#12, Suite Westfield</address>
      </li>
    </ul>

    <div class="swoosh-area" role="img" aria-label="Large brand swoosh graphic in pale, sky and mid blue sweeping into white"></div>
  </section>

  <section class="card card--back">
    <div class="pattern-area" role="img" aria-label="Repeating brand symbol pattern in tonal blues"></div>
    <div class="wordmark">MRT Property</div>
  </section>
</body>
</html>
```